Business Card Design

We need a business card designed for our new company. Prefer a black card with white logo & writing.

Contact Information for Business Card

Ted Galloway, address: 7-4812 Fernhollow Road, Abbotsford, BC, V3K 8R2, Office Phone: 604-712-3390, Cell: 604-947-2164, Email: ted@resinworkshub.ca

Colors

Designer to choose only greyscale colors for use in the design.

```html
<!DOCTYPE html>
<html lang="en">
<head>
<meta charset="utf-8">
<title>Resinworks Hub – Business Card</title>
<link href="https://fonts.googleapis.com/css2?family=Montserrat:wght@400;500;700;800&display=swap" rel="stylesheet">
<style>
  :root {
    --backdrop: #1e1e1e;
    --card: #000000;
    --ink: #ffffff;
    --disc: #ffffff;
  }
  * { margin: 0; padding: 0; box-sizing: border-box; }
  html, body {
    width: 1200px; height: 900px; overflow: hidden;
    background: var(--backdrop);
    font-family: "Montserrat", sans-serif;
    color: var(--ink);
  }
  .card {
    position: absolute;
    left: 341px;
    width: 518px; height: 296px;
    background: var(--card);
    overflow: hidden;
  }
  .card--front { top: 141px; }
  .card--back { top: 463px; }

  .disc {
    position: absolute;
    width: 288px; height: 288px;
    border-radius: 50%;
    background: var(--disc);
  }
  .card--front .disc { left: 276px; top: -1px; }
  .card--back .disc { left: -45px; top: 4px; }

  .wordmark {
    font-weight: 800;
    letter-spacing: 0.5px;
    line-height: 1;
  }
  .card--front .wordmark {
    position: absolute; left: 27px; top: 27px;
    font-size: 29px;
  }
  .person {
    position: absolute; left: 27px; top: 100px;
  }
  .person__name {
    font-weight: 700; font-size: 17px; letter-spacing: 0.3px; line-height: 1.2;
  }
  .person__title {
    font-weight: 400; font-size: 13.5px; line-height: 1.3;
  }
  .address {
    position: absolute; left: 27px; top: 152px;
    font-size: 13.5px; line-height: 18px; font-style: normal;
  }
  .contacts {
    position: absolute; left: 27px; top: 201px;
    list-style: none; font-size: 13.5px; line-height: 18px;
  }
  .contacts li { display: flex; align-items: center; gap: 5px; }
  .contacts svg { width: 13px; height: 13px; fill: var(--ink); flex: none; }

  .back-brand {
    position: absolute; left: 245px; top: 0; width: 273px; height: 296px;
    display: flex; flex-direction: column; align-items: center; justify-content: center; gap: 8px;
  }
  .back-brand .wordmark { font-size: 30px; }
  .back-brand .wordmark--sub { font-size: 14px; letter-spacing: 6px; }
</style>
</head>
<body>
  <section class="card card--front">
    <div class="disc"></div>
    <div class="wordmark">RESINWORKS</div>
    <div class="person">
      <div class="person__name">TED GALLOWAY</div>
      <div class="person__title">President</div>
    </div>
    <address class="address">
      7-4812 Fernhollow Road<br>
      Abbotsford, BC, V3K 8R2
    </address>
    <ul class="contacts">
      <li><svg viewBox="0 0 24 24"><path d="M6.6 10.8a15.1 15.1 0 0 0 6.6 6.6l2.2-2.2a1 1 0 0 1 1-.25 11.4 11.4 0 0 0 3.6.57 1 1 0 0 1 1 1V20a1 1 0 0 1-1 1A17 17 0 0 1 3 4a1 1 0 0 1 1-1h3.5a1 1 0 0 1 1 1c0 1.25.2 2.45.57 3.57a1 1 0 0 1-.25 1z"/></svg>604-712-3390</li>
      <li><svg viewBox="0 0 24 24"><path d="M7 1h10a2 2 0 0 1 2 2v18a2 2 0 0 1-2 2H7a2 2 0 0 1-2-2V3a2 2 0 0 1 2-2zm0 3v15h10V4zm5 16.2a1 1 0 1 0 0 2 1 1 0 0 0 0-2z"/></svg>604-947-2164</li>
      <li><svg viewBox="0 0 24 24"><path d="M2 5h20v2l-10 6L2 7zm0 4 10 6 10-6v10H2z"/></svg>ted@resinworkshub.ca</li>
      <li><svg viewBox="0 0 24 24" fill="none"><g fill="none" stroke="#fff" stroke-width="1.8"><circle cx="12" cy="12" r="10"/><ellipse cx="12" cy="12" rx="4.5" ry="10"/><path d="M2 12h20M4 6.5h16M4 17.5h16"/></g></svg>resinworkshub.ca</li>
    </ul>
  </section>

  <section class="card card--back">
    <div class="disc"></div>
    <div class="back-brand">
      <div class="wordmark">RESINWORKS</div>
      <div class="wordmark wordmark--sub">HUB</div>
    </div>
  </section>
</body>
</html>
```